Mira Bloom Fitness Coaching Project

I am a personal trainer based in London. My services include one-on-one PT sessions, bootcamps.
I would like the design to be minimalistic. With light colours: white, pink, purple.
I specialise in weight loss, flexibility, mobility.

Tessa Brogan
Personal Trainer
Email: tessa.brogan@quellmail.com
tel: 07700218493
Instagram: Mira Bloom

Target Market(s)

adults, mostly females (age 18-50).

Industry/Entity Type

Fitness

Contact Information for Business Card

Tessa Brogan
Personal Trainer
tel: 07700218493
Instagram: Mira Bloom

Font styles to use
Serif

Colors
eea4c8
fbd4d5
fdf9cf
cfeae6
cee9f5

Requirements
Nice to have
• minimalistic style
• easy to read and remember

```html
<!DOCTYPE html>
<html lang="en">
<head>
<meta charset="utf-8">
<title>Tessa Brogan – Personal Trainer Business Cards</title>
<link rel="stylesheet" href="https://fonts.googleapis.com/css2?family=Montserrat:wght@300;400;500&family=Open+Sans:wght@400&display=swap">
<style>
  :root {
    --backdrop: #e6e6e1;
    --card-grey: #6b6b6b;
    --card-white: #fdfdfc;
    --edge-pink: #b9739f;
    --brand-pink: #eea4c8;
    --ring-pink: #f4c6d6;
    --ink-grey: #7a7a7a;
    --ink-dark: #2e2e2e;
    --foil-white: #f2f2f2;
  }
  * { margin: 0; padding: 0; box-sizing: border-box; }
  html, body { width: 1200px; height: 1200px; overflow: hidden; }
  body {
    background: var(--backdrop);
    position: relative;
    font-family: "Montserrat", sans-serif;
  }
  .card {
    position: absolute;
    width: 560px;
    height: 320px;
    border-bottom: 6px solid var(--edge-pink);
    box-shadow: 0 10px 24px rgba(0,0,0,0.18);
  }
  .card--front { left: 110px; top: 130px; background: var(--card-grey); }
  .card--back  { left: 530px; top: 500px; background: var(--card-white); }

  .brand {
    position: absolute;
    display: flex;
    align-items: center;
    gap: 16px;
  }
  .brand__ring {
    width: 74px; height: 74px;
    border-radius: 50%;
    border: 2px solid currentColor;
    flex: none;
  }
  .brand__name {
    font-weight: 400;
    font-size: 34px;
    letter-spacing: -0.5px;
    text-transform: uppercase;
    line-height: 1;
  }
  .brand__role {
    font-family: "Montserrat", sans-serif;
    font-weight: 300;
    font-size: 13px;
    letter-spacing: 5px;
    text-transform: uppercase;
    margin-top: 8px;
  }

  .card--front .brand { left: 120px; top: 120px; color: var(--foil-white); }
  .card--front .brand__role { color: var(--foil-white); }

  .card--back .brand { left: 40px; top: 125px; color: var(--brand-pink); }
  .card--back .brand__name { font-size: 26px; }
  .card--back .brand__ring { width: 56px; height: 56px; border-color: var(--ring-pink); }
  .card--back .brand__role { color: var(--ink-grey); font-size: 10px; letter-spacing: 4px; }

  .contacts {
    position: absolute;
    left: 330px; top: 110px;
    list-style: none;
    font-family: "Open Sans", sans-serif;
    font-size: 14px;
    color: var(--ink-dark);
  }
  .contacts li { display: flex; align-items: center; gap: 8px; margin-bottom: 12px; }
  .contacts svg { width: 14px; height: 14px; flex: none; }
  .contacts .contact--social { color: var(--brand-pink); }
  .social-square { width: 11px; height: 11px; border: 1.5px solid var(--brand-pink); flex: none; }

  .brand--standalone { left: 80px; top: 930px; color: var(--brand-pink); }
  .brand--standalone .brand__name { font-size: 44px; }
  .brand--standalone .brand__ring { width: 150px; height: 150px; border-color: var(--ring-pink); border-width: 3px; }
  .brand--standalone .brand__role { color: var(--ink-grey); font-size: 18px; letter-spacing: 7px; }
</style>
</head>
<body>

  <section class="card card--front" aria-label="Business card front">
    <div class="brand">
      <div>
        <p class="brand__name">Tessa Brogan</p>
        <p class="brand__role">Personal Trainer</p>
      </div>
      <span class="brand__ring"></span>
    </div>
  </section>

  <section class="card card--back" aria-label="Business card back">
    <div class="brand">
      <div>
        <p class="brand__name">Tessa Brogan</p>
        <p class="brand__role">Personal Trainer</p>
      </div>
      <span class="brand__ring"></span>
    </div>
    <ul class="contacts">
      <li>
        <svg viewBox="0 0 16 16" aria-hidden="true"><rect x="1" y="3" width="14" height="10" rx="1" fill="none" stroke="#eea4c8" stroke-width="1.6"/><path d="M1 4l7 5 7-5" fill="none" stroke="#eea4c8" stroke-width="1.6"/></svg>
        tessa.brogan@quellmail.com
      </li>
      <li>
        <svg viewBox="0 0 16 16" aria-hidden="true"><path d="M4 1.5l2.2 3-1.3 1.6a8 8 0 0 0 5 5l1.6-1.3 3 2.2-1.5 2.5C7 14 2 9 1.5 3z" fill="#eea4c8"/></svg>
        07700218493
      </li>
      <li class="contact--social">
        <span class="social-square"></span>
        Mira Bloom
      </li>
    </ul>
  </section>

  <div class="brand brand--standalone">
    <div>
      <p class="brand__name">Tessa Brogan</p>
      <p class="brand__role">Personal Trainer</p>
    </div>
    <span class="brand__ring"></span>
  </div>

</body>
</html>
```